American cannabis tech company business card design

Pavrel.com is seeking a modern, professional, and brand-aligned business card that represents our company and its core values: Mission, Story, Values, and Impact. As an innovative cannabis company, we want a business card that is not only visually appealing but also serves as a representation of who we are and what we stand for.

Project Scope: Design a double-sided business card that integrates our brand identity and core values. Incorporate our key brand elements, ensuring a sleek and contemporary aesthetic. Visually reflect our core values (Mission, Story, Values, Impact) in a way that is engaging yet professional.

Target Market(s)

Vendors, third parties,

Contact Information for Business Card

Contact details (name, title, email, phone, website, etc.)

Font styles to use
Other font styles liked:
• Caslon, Centra

Colors

Designer to choose colors to be used in the design.

Requirements
Must have
• Pavrel.com logo and branding A creative yet clean way to integrate our core values (Mission, Story, Values, Impact) Modern typography and a well-structured layout
Nice to have
• forest green, grey, white, black
Should not have
• references to marijuana, leafs, plants, or related product

```html
<!DOCTYPE html>
<html lang="en">
<head>
<meta charset="UTF-8">
<title>Pavrel Business Card</title>
<link href="https://fonts.googleapis.com/css2?family=Poppins:wght@400;500;600;700;800&display=swap" rel="stylesheet">
<style>
  :root {
    --forest: #1a3a1c;
    --forest-deep: #14301a;
    --ink-green: #163218;
    --paper: #ececec;
    --paper-light: #f4f4f4;
    --text-light: #f2f2f2;
    --backdrop: #2b2b2b;
  }
  * { margin: 0; padding: 0; box-sizing: border-box; }
  html, body {
    width: 1200px; height: 1200px; overflow: hidden;
    background: var(--backdrop);
    font-family: "Poppins", sans-serif;
  }
  .stage { position: relative; width: 1200px; height: 1200px; }

  .card {
    position: absolute; left: 201px; width: 797px; height: 454px;
    border-radius: 20px; overflow: hidden;
    box-shadow: 0 12px 30px rgba(0,0,0,0.45);
  }
  .card--front { top: 96px; background: var(--forest); }
  .card--back { top: 656px; background: var(--forest); color: var(--text-light); }

  .front-top {
    position: absolute; left: 0; top: 0; width: 100%; height: 253px;
    background: linear-gradient(180deg, var(--paper-light), var(--paper));
    display: flex; align-items: center; justify-content: center;
  }
  .wordmark {
    font-weight: 800; font-size: 104px; letter-spacing: 2px;
    color: var(--ink-green); line-height: 1; margin-top: -28px;
  }

  .identity {
    position: absolute; right: 408px; top: 318px; text-align: right;
    color: var(--text-light);
  }
  .identity__name { font-weight: 700; font-size: 34px; line-height: 1.1; letter-spacing: 0.5px; }
  .identity__title { font-weight: 400; font-size: 21px; line-height: 1.4; }

  .divider {
    position: absolute; left: 418px; top: 314px; width: 2px; height: 78px;
    background: var(--text-light);
  }

  .contacts { position: absolute; left: 446px; top: 302px; list-style: none; color: var(--text-light); }
  .contacts li {
    display: flex; align-items: center; height: 32px;
    font-size: 20px; letter-spacing: 0.8px;
  }
  .contacts svg { width: 18px; height: 18px; margin-right: 16px; flex: none; }

  .value-block { position: absolute; width: 330px; }
  .value-block h2 {
    display: inline-block; font-weight: 800; font-size: 18px; letter-spacing: 0.3px;
    padding-bottom: 1px; border-bottom: 2px solid var(--text-light); margin-bottom: 9px;
  }
  .value-block p { font-size: 15.2px; line-height: 18.7px; font-weight: 400; }
  .value-block--wide { width: 362px; }
</style>
</head>
<body>
<div class="stage">

  <section class="card card--front">
    <div class="front-top">
      <div class="wordmark">PAVREL</div>
    </div>

    <div class="identity">
      <div class="identity__name">DANIEL CARVER</div>
      <div class="identity__title">Co-founder &amp; CEO</div>
    </div>
    <div class="divider"></div>

    <ul class="contacts">
      <li>
        <svg viewBox="0 0 24 24" fill="none" stroke="#f2f2f2" stroke-width="2" stroke-linecap="round" stroke-linejoin="round">
          <path d="M22 16.9v3a2 2 0 0 1-2.2 2 19.8 19.8 0 0 1-8.6-3.1 19.5 19.5 0 0 1-6-6A19.8 19.8 0 0 1 2.1 4.2 2 2 0 0 1 4.1 2h3a2 2 0 0 1 2 1.7c.1 1 .4 1.9.7 2.8a2 2 0 0 1-.5 2.1L8 9.9a16 16 0 0 0 6 6l1.3-1.3a2 2 0 0 1 2.1-.4c.9.3 1.8.6 2.8.7a2 2 0 0 1 1.7 2z"/>
          <path d="M15 3a6 6 0 0 1 6 6M15 7a2 2 0 0 1 2 2"/>
        </svg>
        +1 405-555-0148
      </li>
      <li>
        <svg viewBox="0 0 24 24" fill="none" stroke="#f2f2f2" stroke-width="2" stroke-linejoin="round">
          <rect x="2" y="5" width="20" height="14" rx="1"/>
          <path d="M2 6l10 7 10-7"/>
        </svg>
        team@pavrel.com
      </li>
      <li>
        <svg viewBox="0 0 24 24" fill="none" stroke="#f2f2f2" stroke-width="2">
          <circle cx="12" cy="12" r="10"/>
          <path d="M2 12h20M12 2a15 15 0 0 1 0 20M12 2a15 15 0 0 0 0 20"/>
        </svg>
        pavrel.com
      </li>
    </ul>
  </section>

  <section class="card card--back">
    <div class="value-block" style="left:46px; top:67px;">
      <h2>MISSION</h2>
      <p>We think cannabis should be accessible, affordable, convenient, and transparent. But most importantly, we believe in supporting the American farmers who make all of this possible.</p>
    </div>

    <div class="value-block" style="left:46px; top:213px;">
      <h2>STORY</h2>
      <p>Founded in 2022 by Daniel Carver and Jonah Ellery, Pavrel now has a global team of 200+ full-time employees in addition to our robust network of small, U.S. farmers and manufacturing partners. We've built partnerships with over 50 small American farms, bolstering local economies and promoting sustainable farming practices.</p>
    </div>

    <div class="value-block value-block--wide" style="left:401px; top:67px;">
      <h2>VALUES</h2>
      <p>At our core is a commitment to product quality and world-class customer experiences. Our company culture fosters open communication &amp; open doors: everybody here has a voice, &amp; we believe that by investing in both our people &amp; our customers, we all will rise.</p>
    </div>

    <div class="value-block value-block--wide" style="left:401px; top:250px;">
      <h2>IMPACT</h2>
      <p>Social impact is a business pillar, not an afterthought. This year, we've donated tens of thousands of dollars to pet humane societies. We've contributed to the campaigns of politicians who advocate for cannabis, contributing to the broader movement toward recognition &amp; acceptance.</p>
    </div>
  </section>

</div>
</body>
</html>
```